Need a clean & modern homepage for an education site + opportunity for longer term work

Thanks for viewing our project. We are excited about this new website and we hope that we might build a relationship with designers as we work on this project. I provided quite a few details and requirements to help you more quickly create a design that meets our needs.
Who we are:
We are a website that discusses the importance of college accreditation and provides a directory of college programs.
What we need:
A homepage that meets the below requirements and is inspired by the examples provided
Definition of accredited:
ac·cred·it·ed [uh-kred-i-tid] adj.
1. officially recognized as meeting the essential requirements, as of academic excellence: accredited schools.
2. provided with official credentials, as by a government: an accredited diplomatic representative.
3. accepted as authoritative: an accredited theory.
Overall look and feel for the homepage:
- Clean, simple and modern
- Limited (or zero) pictures
- Utilize color blocks with text
- A trend seems to be longer vertical length homepages with lots of whitespace. I generally like this trend as long as the page is not way to tall.
Inspirations: Sites that have a similar look and feel to what I need.
http://lernvoxa.org/
http://www.campusmetrik.com/colleges/brantmoor-university/
http://quietfolding.org/
http://www.velostrahiring.com/
http://www.zunq.com/
http://sketches.bxv.com/
Items to be included on the homepage. Details below on each item.
- Top navigation
- Logo: Please leave a blank area for a logo. The logo has not been designed.
- Simple graphic/color block at the top that highlights a definition of “Accredited” – the definition should be formatted like it is being copy/pasted from a dictionary.
- Space for a video and small (50 word) written description of the video. You can use placeholder text.
- One section with 3 Paragraphs of content (each paragraph around 100 words) with a header at the top. You can use placeholder text but please create the formatting. At the end of the 3 paragraphs please have a “Read More” Note this shouldn't be 3 separate paragraphs with three read mores - it is 3 paragraphs with one read more at the end.
- An area with the header “Search Colleges by State” that has anchor text links to all 50 states.
Top navigation:
- Home
- States – with a subnav dropdown that includes all 50 US states.
- Programs – with a subnav dropdown that includes program titles (list below)
- Degrees - with a subnav dropdown that includes 5 degree levels (list below)
- Accreditation – no subnav
- Rankings – no subnav
- Resources – no subnav
Footer
- Link to about us, privacy, and a copyright www.url.com
Programs List for sub navigation
Accounting
Art
Bible
Business
Criminal Justice
Design
Education
Engineering
English
Law
LPN to RN
Management
Math
MBA
MPH
Medical Assisting
Military
Nursing
Occupational Therapy
Paralegal
Psychology
Pharmacy
RN to BSN
Radiology
Social Work
Sonography
Degrees list for sub navigation
Certificate
Associate
Bachelors
Masters
PhD
Thanks so much - looking forward to working with you!
Education

```html
<!DOCTYPE html>
<html lang="en">
<head>
<meta charset="utf-8">
<title>Accredited Colleges – Home</title>
<link href="https://fonts.googleapis.com/css2?family=Ubuntu:ital,wght@0,300;0,400;0,500;0,700;1,400&family=Kreon:wght@400;700&display=swap" rel="stylesheet">
<style>
:root{
  --ink-dark:#353b47;
  --nav-bg:#f3f3f3;
  --nav-text:#7d7d7d;
  --accent-red:#f05a47;
  --board-blue:#1b5fae;
  --board-slate:#444546;
  --band-grey:#ebebe9;
  --card-green:#22b89a;
  --card-teal:#24adc8;
  --card-lilac:#8c8ebf;
  --video-blue:#6699cc;
  --heading-blue:#2a9fd8;
  --body-grey:#8a8a8a;
  --white:#ffffff;
}
*{box-sizing:border-box;margin:0;padding:0}
html,body{width:1200px;height:2544px;overflow:hidden}
body{font-family:"Ubuntu",sans-serif;background:var(--white);position:relative}
.site-header{height:106px;display:flex;align-items:center;justify-content:center}
.logo-text{font-weight:700;font-size:50px;color:#000;letter-spacing:1px}
.main-nav{height:49px;background:var(--nav-bg);position:relative}
.main-nav a{position:absolute;top:0;height:49px;line-height:49px;font-size:14px;font-weight:700;color:var(--nav-text);text-decoration:none;letter-spacing:.5px}
.main-nav a.is-active{background:var(--accent-red);color:var(--white);width:115px;text-align:center}
.caret{display:inline-block;margin-left:10px;border-left:4px solid transparent;border-right:4px solid transparent;border-top:5px solid var(--nav-text);vertical-align:middle}
.hero{height:453px;background:var(--ink-dark);position:relative}
.hero-board{position:absolute;left:123px;top:0;width:1001px;height:453px;background:linear-gradient(to bottom,var(--board-slate) 0%,var(--board-slate) 72%,var(--board-blue) 100%)}
.definition{position:absolute;left:307px;top:75px;color:var(--white);font-family:"Kreon",serif}
.word{font-size:44px;font-weight:400;letter-spacing:1px}
.pron{font-size:25px;margin-left:10px}
.part{font-family:"Ubuntu",sans-serif;font-style:italic;font-size:26px;margin-top:-2px}
.senses{margin-top:28px;font-size:17px;line-height:22px;list-style:none;width:560px}
.senses li{padding-left:18px;text-indent:-18px}
.features{height:372px;background:var(--band-grey);position:relative}
.card{position:absolute;top:39px;width:288px;height:300px;color:var(--white);text-align:center;padding:28px 22px 0}
.card--ranking{left:148px;background:var(--card-green)}
.card--accreditation{left:456px;background:var(--card-teal)}
.card--resources{left:761px;background:var(--card-lilac)}
.card-icon{width:62px;height:62px;margin:0 auto;display:block}
.card h2{font-weight:300;font-size:38px;margin:6px 0 8px}
.card p{font-size:13px;font-weight:500;line-height:17px}
.video-band{height:472px;background:var(--video-blue);text-align:center;color:var(--white);position:relative}
.video-band h2{font-weight:300;font-size:42px;padding-top:30px;letter-spacing:1px}
.player{position:absolute;left:367px;top:95px;width:436px;height:235px;background:var(--white)}
.player-screen{height:187px;background:linear-gradient(135deg,#8d8173,#5d5348 50%,#3c3a36)}
.player-controls{height:48px;position:relative}
.progress{position:absolute;left:60px;top:21px;width:312px;height:10px;background:#d6dde5}
.progress span{display:block;width:46%;height:100%;background:#f07a70}
.video-copy{position:absolute;left:159px;top:344px;width:880px;font-size:18px;line-height:23px}
.article{height:478px;padding:40px 148px 0}
.article h2{font-weight:300;font-size:37px;color:var(--heading-blue)}
.article-body{margin-top:30px;font-size:16px;line-height:27px;color:var(--body-grey)}
.article-body p+p{margin-top:27px}
.readmore{display:inline-block;margin-top:34px;width:123px;height:40px;line-height:38px;border:2px solid var(--accent-red);color:var(--accent-red);text-align:center;font-size:14px;text-decoration:none}
.states{height:358px;background:var(--accent-red);color:var(--white);position:relative}
.states-title{position:absolute;top:36px;left:148px;width:900px;display:flex;align-items:center;gap:20px}
.states-title::before,.states-title::after{content:"";flex:1;height:1px;background:rgba(255,255,255,.7)}
.states-title h2{font-weight:300;font-size:34px}
.state-grid{position:absolute;top:112px;left:167px;width:920px;display:grid;grid-template-columns:155px 157px 146px 151px 161px 150px;row-gap:11px}
.state-grid a{color:var(--white);font-style:italic;font-size:17px;line-height:23px}
.site-footer{height:256px;background:var(--ink-dark);color:var(--white);text-align:center;padding-top:30px}
.site-footer .logo-text{color:var(--white);font-size:38px}
.social{display:flex;justify-content:center;gap:4px;margin-top:26px}
.social span{width:36px;height:36px}
.footer-links{margin-top:28px;font-size:16px}
.footer-links a{color:var(--white);text-decoration:none;margin:0 10px}
.footer-url{margin-top:14px;font-style:italic;font-size:15px}
</style>
</head>
<body>
<header class="site-header"><span class="logo-text">LOGO</span></header>
<nav class="main-nav">
  <a href="#" class="is-active" style="left:148px">HOME</a>
  <a href="#" style="left:290px">STATES<i class="caret"></i></a>
  <a href="#" style="left:398px">PROGRAMS<i class="caret"></i></a>
  <a href="#" style="left:538px">DEGREES<i class="caret"></i></a>
  <a href="#" style="left:657px">ACCREDITATION</a>
  <a href="#" style="left:822px">RANKINGS</a>
  <a href="#" style="left:943px">RESOURCES</a>
</nav>
<section class="hero">
  <div class="hero-board" role="img" aria-label="Illustration of a classroom chalkboard with eraser and chalk"></div>
  <div class="definition">
    <div><span class="word">ac·cred·it·ed</span><span class="pron">[uh-kred-i-tid]</span></div>
    <div class="part">adj</div>
    <ol class="senses">
      <li>1. officially recognized as meeting the essential requirements, as of academic excellence: accredited schools.</li>
      <li>2. provided with official credentials, as by a government: an accredited diplomatic representative.</li>
      <li>3. accepted as authoritative: an accredited theory.</li>
    </ol>
  </div>
</section>
<section class="features">
  <article class="card card--ranking">
    <svg class="card-icon" viewBox="0 0 62 62"><circle cx="31" cy="31" r="31" fill="#fff" opacity=".9"/><path d="M22 18h18v8a9 9 0 0 1-18 0z M29 34h4v8h-4z M24 44h14v3H24z" fill="#6b7c88"/></svg>
    <h2>Ranking</h2>
    <p>Lorem ipsum dolor sit amet, consectetur adipiscing elit. Fusce rutrum magna in nisi mattis, ut mollis lorem dictum. Morbi ac condimentum lacus. Phasellus dolor magna, rhoncus et interdum eget, tempor non sapien.</p>
  </article>
  <article class="card card--accreditation">
    <svg class="card-icon" viewBox="0 0 62 62"><circle cx="31" cy="31" r="31" fill="#fff" opacity=".9"/><circle cx="31" cy="28" r="11" fill="#6b7c88"/><path d="M24 37l-4 12 6-3 3 5 2-13z M38 37l4 12-6-3-3 5-2-13z" fill="#6b7c88"/></svg>
    <h2>Accreditation</h2>
    <p>Lorem ipsum dolor sit amet, consectetur adipiscing elit. Fusce rutrum magna in nisi mattis, ut mollis lorem dictum. Morbi ac condimentum lacus. Phasellus dolor magna, rhoncus et interdum eget, tempor non sapien.</p>
  </article>
  <article class="card card--resources">
    <svg class="card-icon" viewBox="0 0 62 62"><circle cx="31" cy="31" r="31" fill="#fff" opacity=".9"/><path d="M31 18l20 9-20 9-20-9z M20 32v8c6 5 16 5 22 0v-8l-11 5z" fill="#6b7c88"/></svg>
    <h2>Resources</h2>
    <p>Lorem ipsum dolor sit amet, consectetur adipiscing elit. Fusce rutrum magna in nisi mattis, ut mollis lorem dictum. Morbi ac condimentum lacus. Phasellus dolor magna, rhoncus et interdum eget, tempor non sapien.</p>
  </article>
</section>
<section class="video-band">
  <h2>WATCH OUR VIDEO</h2>
  <div class="player">
    <div class="player-screen" role="img" aria-label="Video still of a presenter speaking to camera"></div>
    <svg style="position:absolute;left:184px;top:59px" width="70" height="70" viewBox="0 0 70 70"><circle cx="35" cy="35" r="32" fill="rgba(255,255,255,.35)" stroke="#fff" stroke-width="3"/><path d="M27 21l22 14-22 14z" fill="#fff"/></svg>
    <div class="player-controls">
      <svg style="position:absolute;left:14px;top:12px" width="26" height="26" viewBox="0 0 26 26"><circle cx="13" cy="13" r="12" fill="#6c7f90"/><path d="M10 7l9 6-9 6z" fill="#fff"/></svg>
      <div class="progress"><span></span></div>
      <svg style="position:absolute;left:396px;top:13px" width="24" height="24" viewBox="0 0 24 24" stroke="#9aa6b2" stroke-width="2.5" fill="none"><path d="M2 2l7 7M22 2l-7 7M2 22l7-7M22 22l-7-7M2 8V2h6M16 2h6v6M2 16v6h6M22 16v6h-6"/></svg>
    </div>
  </div>
  <p class="video-copy">Lorem ipsum dolor sit amet, consectetur adipiscing elit. Fusce rutrum magna in nisi mattis, ut mollis lorem dictum. Morbi ac condimentum lacus. Phasellus dolor magna, rhoncus et interdum eget, tempor non sapien. Nullam fermentum ultrices ipsum non molestie. Nunc vitae nulla ut felis ultrices mollis nec vel felis. Sed vehicula orci a orci vehicula mattis.</p>
</section>
<section class="article">
  <h2>HEADER TITLE 1</h2>
  <div class="article-body">
    <p>Lorem ipsum dolor sit amet, consectetur adipiscing elit. Donec accumsan nec ipsum a auctor. Nulla facilisi. Aliquam erat volutpat. Mauris suscipit diam a eros faucibus, non imperdiet urna porttitor. Nulla at faucibus libero. Donec congue tincidunt volutpat.</p>
    <p>Nulla facilisi. Nulla sit amet vehicula ante. Nunc non sapien neque. In suscipit hendrerit metus id pellentesque.<br>Proin volutpat turpis et rutrum congue. Curabitur eget ipsum volutpat, mollis est in, rutrum velit. Vivamus tellus elit, lacinia ac ullamcorper in, commodo nec nibh.</p>
    <p>Pellentesque sit amet urna nec sem pulvinar pellentesque a a lorem.<br>Proin id ultrices urna. Fusce sed nisi sed augue vehicula semper a consequat nunc. Maecenas eu feugiat erat. Integer tincidunt.</p>
  </div>
  <a href="#" class="readmore">READMORE</a>
</section>
<section class="states">
  <div class="states-title"><h2>Search Colleges by State</h2></div>
  <div class="state-grid">
    <a href="#">California</a><a href="#">Kentucky</a><a href="#">Louisiana</a><a href="#">California</a><a href="#">Kentucky</a><a href="#">Louisiana</a>
    <a href="#">Texas</a><a href="#">Florida</a><a href="#">Arizona</a><a href="#">Texas</a><a href="#">Florida</a><a href="#">Arizona</a>
    <a href="#">Illinois</a><a href="#">New Jersy</a><a href="#">Georgia</a><a href="#">Illinois</a><a href="#">New Jersy</a><a href="#">Georgia</a>
    <a href="#">Virginia</a><a href="#">Pennsylvania</a><a href="#">Tennessee</a><a href="#">Virginia</a><a href="#">Pennsylvania</a><a href="#">Tennessee</a>
    <a href="#">Massachusetts</a><a href="#">Alaska</a><a href="#">Colorado</a><a href="#">Massachusetts</a><a href="#">Alaska</a><a href="#">Colorado</a>
  </div>
</section>
<footer class="site-footer">
  <span class="logo-text">LOGO</span>
  <div class="social">
    <span style="background:#3b5ea6"></span><span style="background:#2aa3dc"></span><span style="background:#d1402f"></span><span style="background:#c8232c"></span>
  </div>
  <div class="footer-links"><a href="#">about us</a>|<a href="#">privacy</a>|<a href="#">copyright</a></div>
  <div class="footer-url">www.url.com</div>
</footer>
</body>
</html>
```